Real Estate Media Company Business Card

’m looking for a modern, high-end, double-sided business card for:
Bright Harbor Studios LLC
(Real Estate Photography & Videography)
The design should feel clean, minimal, and premium, appealing to top real estate agents and brokers.
👉 Horizontal layout is preferred
👉 Vertical option is welcome but not required
⸻
Front Side (Main Information):
Include:
* Desmond Whitfield
* Bright Harbor Studios LLC
* Title (open to creative improvement)
* Phone Number
* Email
* Website
⸻
Services Section (VERY IMPORTANT):
This should be a key visual element, not an afterthought.
Services to Include:
* Cinematic Video
* Real Estate Photography
* Drone
* Social Media Reels
* Floor Plans
* Use clean, modern icons next to each service
* Icons should be simple, minimal, and consistent style (outline or thin line preferred)
* Option to place icons inside small circles (like reference)
Layout:
* Format services similar to a clean horizontal or grid-style list (like “example 2”)
* Keep spacing balanced and uncluttered
* Make this section visually appealing and easy to scan
⸻
Back Side:
* Keep it extremely minimal
* Only include the logo in a corner
* No additional text needed
⸻
Typography & Style:
* Modern, clean, slightly bold fonts (based on uploaded references)
* Strong hierarchy (name + services stand out most)
* Plenty of white/negative space
* Avoid clutter
⸻
Overall Feel:
* Luxury
* Modern
* Clean
* Confident
* High-end real estate branding
⸻
Notes for Designers:
* Simplicity is key
* Services section should feel polished and intentional
* This card should feel like something a top-producing real estate agent would keep
Target Market(s)
Real estate agent agents

```html
<!DOCTYPE html>
<html lang="en">
<head>
<meta charset="utf-8">
<title>Bright Harbor Studios – Business Card</title>
<link rel="stylesheet" href="https://fonts.googleapis.com/css2?family=Montserrat:wght@400;500&family=Playfair+Display:wght@500;600&display=swap">
<style>
  :root {
    --page: #e0e0e0;
    --green-dark: #142a23;
    --green-mid: #1b3a30;
    --green-line: #5f7d72;
    --orange: #ef8a17;
    --white: #ffffff;
    --ink: #1a1a1a;
  }
  * { margin: 0; padding: 0; box-sizing: border-box; }
  html, body { width: 923px; height: 1200px; overflow: hidden; background: var(--page); }
  body { position: relative; font-family: "Montserrat", sans-serif; color: var(--white); }

  .card {
    position: absolute; left: 96px; width: 731px; height: 418px; overflow: hidden;
    box-shadow: 0 6px 18px rgba(0,0,0,.28);
  }
  .card--front { top: 105px; }
  .card--back { top: 677px; background: var(--white); }

  .interior-art {
    position: absolute; inset: 0;
    background: linear-gradient(120deg, var(--green-dark) 0%, #16302a 55%, var(--green-mid) 100%);
  }

  .brand-name {
    position: absolute; text-align: center;
    font-family: "Montserrat", sans-serif; font-weight: 500;
    font-size: 23px; letter-spacing: 2.5px; line-height: 1.25;
  }
  .card--front .brand-name { left: 468px; top: 92px; width: 262px; color: var(--white); }
  .card--back .brand-name { left: 476px; top: 165px; width: 262px; color: var(--ink); }

  .info-panel {
    position: absolute; left: 0; top: 0; width: 435px; height: 418px; overflow: hidden;
  }
  .info-frame {
    position: absolute; left: 29px; top: 26px; width: 420px; height: 362px;
    border: 1px solid var(--green-line);
  }

  .person-name {
    position: absolute; left: 49px; top: 60px;
    font-family: "Playfair Display", serif; font-weight: 600; font-size: 31px; white-space: nowrap;
  }
  .person-name .accent, .services-title .accent { color: var(--orange); }
  .person-title {
    position: absolute; left: 49px; top: 98px; font-size: 17px; letter-spacing: 4.5px; font-weight: 500;
  }

  .contact-list { position: absolute; left: 49px; top: 134px; list-style: none; }
  .contact-list li { display: flex; align-items: center; gap: 9px; height: 23.5px; font-size: 13.5px; }
  .contact-list svg { width: 15px; height: 15px; flex: none; }

  .services-title {
    position: absolute; left: 49px; top: 224px;
    font-family: "Playfair Display", serif; font-weight: 500; font-size: 17px;
  }

  .service { position: absolute; display: flex; align-items: center; gap: 8px; font-size: 12px; white-space: nowrap; }
  .service-icon {
    width: 28px; height: 28px; border: 1px solid var(--orange); border-radius: 50%;
    display: flex; align-items: center; justify-content: center; flex: none;
  }
  .service-icon svg { width: 14px; height: 14px; }

  .divider-v { position: absolute; width: 0; border-left: 1px dashed #cfd8d4; }
  .divider-h { position: absolute; height: 0; border-top: 1px dashed #cfd8d4; }
</style>
</head>
<body>

  <section class="card card--front">
    <div class="interior-art" role="img" aria-label="Faint line drawing of a furnished open-plan kitchen and living room"></div>
    <div class="brand-name">BRIGHT HARBOR<br>STUDIOS</div>
  </section>

  <section class="card card--back">
    <div class="info-panel">
      <div class="interior-art" role="img" aria-label="Faint line drawing of a furnished interior behind the contact details"></div>
      <div class="info-frame"></div>

      <h1 class="person-name">Desmond <span class="accent">Whitfield</span></h1>
      <p class="person-title">Owner</p>

      <ul class="contact-list">
        <li>
          <svg viewBox="0 0 24 24" fill="none" stroke="#ef8a17" stroke-width="2.2" stroke-linecap="round"><path d="M5 3h4l2 5-2.5 1.5a11 11 0 0 0 6 6L16 13l5 2v4a2 2 0 0 1-2 2A16 16 0 0 1 3 5a2 2 0 0 1 2-2z"/></svg>
          555-204-7718
        </li>
        <li>
          <svg viewBox="0 0 24 24"><rect x="2" y="5" width="20" height="14" fill="#ef8a17"/><path d="M2 5l10 8 10-8" fill="none" stroke="#142a23" stroke-width="1.6"/></svg>
          desmond@brightharborstudios.com
        </li>
        <li>
          <svg viewBox="0 0 24 24" fill="none" stroke="#ef8a17" stroke-width="2"><circle cx="12" cy="12" r="9"/><path d="M3 12h18M12 3c3 3 3 15 0 18M12 3c-3 3-3 15 0 18"/></svg>
          brightharborstudios.com
        </li>
      </ul>

      <h2 class="services-title">Our <span class="accent">Services</span></h2>

      <div class="service" style="left:49px;top:263px">
        <span class="service-icon"><svg viewBox="0 0 24 24" fill="none" stroke="#fff" stroke-width="1.6"><rect x="2" y="6" width="14" height="12" rx="2"/><path d="M16 10l6-3v10l-6-3z"/></svg></span>
        Cinematic Video
      </div>
      <div class="divider-v" style="left:204px;top:263px;height:37px"></div>

      <div class="service" style="left:217px;top:263px">
        <span class="service-icon"><svg viewBox="0 0 24 24" fill="none" stroke="#fff" stroke-width="1.6"><rect x="3" y="3" width="18" height="18"/><path d="M3 12h9V3M12 16v5M16 12h5"/></svg></span>
        Floor Plans
      </div>
      <div class="divider-v" style="left:329px;top:263px;height:37px"></div>

      <div class="service" style="left:341px;top:263px">
        <span class="service-icon"><svg viewBox="0 0 24 24" fill="none" stroke="#fff" stroke-width="1.6"><path d="M2 6h7M15 6h7M5 6v3h14V6"/><rect x="8" y="9" width="8" height="5" rx="1"/><path d="M9 14l-2 4M15 14l2 4"/></svg></span>
        Drone
      </div>

      <div class="divider-h" style="left:52px;top:307px;width:140px"></div>
      <div class="divider-h" style="left:218px;top:307px;width:198px"></div>

      <div class="service" style="left:49px;top:322px">
        <span class="service-icon"><svg viewBox="0 0 24 24" fill="none" stroke="#fff" stroke-width="1.6"><rect x="3" y="3" width="18" height="18" rx="4"/><path d="M3 8h18M8 3l2 5M14 3l2 5"/><path d="M10 11v6l5-3z"/></svg></span>
        Social Media Reels
      </div>
      <div class="divider-v" style="left:204px;top:311px;height:36px"></div>

      <div class="service" style="left:217px;top:322px">
        <span class="service-icon"><svg viewBox="0 0 24 24" fill="none" stroke="#fff" stroke-width="1.6"><path d="M3 8h4l2-3h6l2 3h4v11H3z"/><circle cx="12" cy="13" r="3.5"/></svg></span>
        Real Estate Photography
      </div>
    </div>

    <div class="brand-name">BRIGHT HARBOR<br>STUDIOS</div>
  </section>

</body>
</html>
```